Thornvale Group needs a business card design

We need a new business card design using the logo recently selected in a logo competition on Pixel Bazaar. Our business is a consultancy specializing in aviation and energy and the winning business card design will promote an image of precision and professionalism with creativity.

Please use the logo with the name on the front of the card and use a complementary font. Make the back white with either the light grey or dark grey logo.

Target Market(s)

Senior finance and legal leaders at aviation and energy companies

Industry/Entity Type

Management Consulting

Contact Information for Business Card

Peter Castrell
President
Thornvale Group

www.thornvalegroup.example

(555) 204-6391
pc@thornvalegroup.example

Requirements
Must have
• Professional font that goes well with the logo font

```html
<!DOCTYPE html>
<html lang="en">
<head>
<meta charset="utf-8">
<title>Thornvale Group – Business Card</title>
<link rel="stylesheet" href="https://fonts.googleapis.com/css2?family=Montserrat:wght@300;400;500&display=swap">
<style>
  :root {
    --navy: #1d4a7e;
    --navy-deep: #173e6c;
    --ink: #4a4a4a;
    --muted: #6d6d6d;
    --paper: #ffffff;
    --ground: #e9e7e3;
  }
  * { box-sizing: border-box; margin: 0; padding: 0; }
  html, body { width: 1200px; height: 950px; overflow: hidden; }
  body {
    background: var(--ground);
    font-family: "Montserrat", sans-serif;
    display: flex;
    align-items: center;
    justify-content: center;
    gap: 80px;
  }

  /* Card back: navy with brand name */
  .card-back {
    width: 580px;
    height: 350px;
    background: var(--navy);
    border: 10px solid var(--paper);
    box-shadow: 0 6px 18px rgba(0,0,0,.18);
    display: flex;
    align-items: center;
    justify-content: center;
    gap: 16px;
  }
  .card-back .brand-square {
    width: 18px; height: 18px; background: var(--paper);
  }
  .card-back .brand-name {
    color: var(--paper);
    font-weight: 400;
    font-size: 30px;
    letter-spacing: 6px;
    text-transform: uppercase;
  }

  /* Card front: white portrait with navy frame */
  .card-front {
    width: 350px;
    height: 580px;
    background: var(--paper);
    border: 9px solid var(--navy);
    box-shadow: 0 6px 18px rgba(0,0,0,.18);
    padding: 52px 40px 40px;
    display: flex;
    flex-direction: column;
  }
  .front-brand {
    display: flex;
    align-items: center;
    gap: 12px;
    color: var(--navy);
    font-weight: 400;
    font-size: 24px;
    letter-spacing: 4px;
    text-transform: uppercase;
    line-height: 1.1;
  }
  .front-brand .brand-square {
    width: 14px; height: 14px; background: var(--navy); flex: none;
  }
  .divider {
    border: 0;
    border-top: 2px dotted var(--navy);
    margin: 30px 0;
    opacity: .7;
  }
  .person-name {
    color: var(--navy);
    font-weight: 500;
    font-size: 22px;
    letter-spacing: 2px;
    text-transform: uppercase;
  }
  .person-title {
    color: var(--muted);
    font-weight: 300;
    font-size: 14px;
    margin-top: 6px;
  }
  .company {
    color: var(--navy);
    font-weight: 400;
    font-size: 15px;
  }
  .services {
    color: var(--ink);
    font-weight: 300;
    font-size: 14px;
    line-height: 1.55;
    margin-top: 4px;
  }
  .contact-list { list-style: none; }
  .contact-list li {
    display: flex;
    align-items: center;
    gap: 10px;
    color: var(--ink);
    font-weight: 300;
    font-size: 13.5px;
    line-height: 1.9;
  }
  .contact-list svg { width: 14px; height: 14px; fill: var(--navy); flex: none; }
</style>
</head>
<body>
  <section class="card-back" aria-label="Card back">
    <span class="brand-square"></span>
    <span class="brand-name">Thornvale Group</span>
  </section>

  <section class="card-front" aria-label="Card front">
    <div class="front-brand">
      <span class="brand-square"></span>
      <span>Thornvale<br>Group</span>
    </div>

    <hr class="divider">

    <h1 class="person-name">Peter Castrell</h1>
    <p class="person-title">President</p>

    <hr class="divider">

    <p class="company">Thornvale Group LLC</p>
    <p class="services">Finance and Strategy Consulting<br>Aviation - Manufacturing - Energy</p>

    <hr class="divider">

    <ul class="contact-list">
      <li>
        <svg viewBox="0 0 16 16" aria-hidden="true"><path d="M3 2c1-1 2 0 3 2s0 2-1 3c1 2 2 3 4 4 1-1 1-2 3-1s3 2 2 3c-1 2-3 2-5 1C5 12 3 10 2 7 1 5 2 3 3 2z"/></svg>
        (555) 204-6391
      </li>
      <li>
        <svg viewBox="0 0 16 16" aria-hidden="true"><path d="M1 3h14v10H1z M2 4l6 5 6-5" fill="none" stroke="#1d4a7e" stroke-width="1.5"/></svg>
        pc@thornvalegroup.example
      </li>
      <li>
        <svg viewBox="0 0 16 16" aria-hidden="true"><circle cx="8" cy="8" r="6.5" fill="none" stroke="#1d4a7e" stroke-width="1.5"/><path d="M1.5 8h13M8 1.5c-3 3-3 10 0 13M8 1.5c3 3 3 10 0 13" fill="none" stroke="#1d4a7e" stroke-width="1.2"/></svg>
        www.thornvalegroup.example
      </li>
    </ul>
  </section>
</body>
</html>
```